International Trade Consulting Firm Seeks Quality Newsletter Design

Our company provides consulting services to Pinnacle 300 type companies. We compete with the largest consulting companies in the world. However, we have the highest level of expertise in the industry and need to look the most professional and high end. We have very relevant and important information to provide our customers about their compliance and projects. We will have the winning design coded to be an e-newsletter, so it needs to be one page. We want to keep our company colors and logo design in the newsletter, they are attached. We DO NOT want it to look like a mini-version of our website. We want a fresh look to this marketing piece. Newsletter will need to include title, possible sub-heading, space for a feature story, 2 other stories included, and space on either the left or right for short cuts, links or highlights of other articles. Contents/'In this issue' section, about us or branding area, section for relevant links, etc...
Pinnacle 300 companies, High-level management
Marketing

```html
<!DOCTYPE html>
<html lang="en">
<head>
<meta charset="utf-8">
<title>TradePoint 411 Newsletter</title>
<link href="https://fonts.googleapis.com/css2?family=Roboto+Condensed:wght@400;700&family=Arimo:wght@400;700&display=swap" rel="stylesheet">
<style>
  :root {
    --stage: #939393;
    --paper: #ffffff;
    --forest: #1f4d22;
    --leaf: #3f8f3a;
    --olive: #8a8a2a;
    --lemon: #f7f39c;
    --highlight: #fbf6ad;
    --charcoal: #2b2b2b;
    --ink: #333333;
    --rule: #c9c98a;
  }
  * { box-sizing: border-box; margin: 0; padding: 0; }
  html, body { width: 1200px; height: 900px; overflow: hidden; }
  body { background: var(--stage); font-family: "Arimo", Arial, sans-serif; color: var(--ink); position: relative; }

  .newsletter { position: absolute; width: 522px; height: 882px; background: var(--paper); box-shadow: 0 2px 6px rgba(0,0,0,.35); overflow: hidden; }
  .newsletter--leaf { left: 63px; top: 20px; }
  .newsletter--team { left: 638px; top: 18px; }

  /* header */
  .masthead { position: absolute; left: 0; top: 0; width: 522px; height: 208px; }
  .brand-panel { position: absolute; left: 0; top: 0; width: 174px; height: 208px; background: linear-gradient(160deg, #3a3a3a, #1e1e1e 70%, #2c3a2a); padding: 38px 0 0 23px; }
  .brand-name { font-family: "Roboto Condensed", Arial, sans-serif; font-weight: 700; font-size: 20px; line-height: 22px; color: var(--leaf); letter-spacing: 1px; }
  .brand-blurb { margin-top: 48px; font-size: 9px; line-height: 14.5px; color: var(--lemon); width: 135px; }
  .brand-blurb u { text-decoration: underline; }
  .hero { position: absolute; left: 174px; top: 0; width: 348px; height: 208px; }
  .hero-leaf { background: linear-gradient(180deg, #d8dfd3 0%, #7aa04f 30%, #5d7f3a 55%, #9a9a95 80%, #6f6f6c 100%); }
  .hero-team { background: linear-gradient(90deg, #6f7f92 0%, #9aa7b6 35%, #c8b9a8 70%, #e6e1dc 100%); }
  .issue-date { position: absolute; right: 18px; top: 20px; font-size: 9px; font-weight: 700; color: #fff; letter-spacing: .3px; }
  .title-ribbon { position: absolute; left: 16px; top: 135px; width: 256px; height: 34px; background: var(--lemon); clip-path: polygon(0 0, 100% 0, 100% 100%, 0 100%, 10px 50%); }
  .title-ribbon .newsletter-title { position: absolute; left: 20px; top: 2px; font-family: "Roboto Condensed", Arial, sans-serif; font-weight: 700; font-size: 31px; line-height: 32px; color: #4a4a3a; white-space: nowrap; }
  .hero-tagline { position: absolute; left: 18px; top: 178px; font-family: "Roboto Condensed", Arial, sans-serif; font-size: 10.5px; color: #fff; white-space: nowrap; }
  .title-box { position: absolute; left: 18px; top: 122px; width: 226px; height: 86px; background: rgba(20,20,20,.82); padding: 8px 0 0 10px; }
  .title-box .newsletter-title { font-family: "Roboto Condensed", Arial, sans-serif; font-weight: 700; font-size: 31px; line-height: 34px; color: var(--lemon); white-space: nowrap; }
  .title-box .tag-strong { font-family: "Roboto Condensed", Arial, sans-serif; font-weight: 700; font-size: 11px; color: #a8c83a; letter-spacing: .4px; margin-top: 2px; white-space: nowrap; }
  .title-box .tag-light { font-size: 9.5px; color: #7fb24a; margin-top: 1px; white-space: nowrap; }

  /* sidebar */
  .sidebar { position: absolute; left: 0; top: 208px; width: 174px; height: 674px; border-right: 1px solid var(--rule); }
  .social-bar { height: 32px; background: var(--charcoal); display: flex; align-items: center; gap: 22px; padding-left: 22px; }
  .social-dot { width: 14px; height: 14px; border-radius: 50%; background: #e6e6e6; }
  .site-url { height: 30px; border-bottom: 1px solid var(--rule); text-align: center; font-size: 10px; font-weight: 700; letter-spacing: 1px; line-height: 30px; color: #444; }
  .contents { border-bottom: 1px solid var(--rule); padding-bottom: 8px; }
  .contents-item { padding: 10px 0 4px 23px; height: 48px; }
  .contents-item h4 { font-family: "Roboto Condensed", Arial, sans-serif; font-weight: 700; font-size: 12.5px; color: var(--forest); }
  .contents-item p { font-size: 7.5px; line-height: 10px; color: #333; width: 140px; margin-top: 1px; }
  .contents-item.is-featured { background: var(--highlight); }
  .ceo-note { padding: 20px 0 0 23px; height: 292px; border-bottom: 1px solid var(--rule); }
  .ceo-head { display: flex; align-items: center; gap: 10px; }
  .ceo-portrait { width: 62px; height: 62px; border-radius: 50%; border: 2px solid #555; background: radial-gradient(circle at 50% 45%, #c9a58c, #7a6a5e); }
  .ceo-name { font-family: "Roboto Condensed", Arial, sans-serif; font-weight: 700; font-size: 10.5px; color: var(--forest); }
  .ceo-role { font-size: 9px; color: var(--leaf); }
  .ceo-note p { font-size: 9px; line-height: 14.5px; color: #222; width: 130px; margin-top: 10px; }
  .ceo-note p + p { margin-top: 14px; }
  .about { padding: 12px 0 0 23px; }
  .about h4 { font-family: "Roboto Condensed", Arial, sans-serif; font-weight: 700; font-size: 12.5px; color: var(--forest); }
  .about svg { display: block; margin: 12px 0 0 46px; }
  .about .about-title { font-size: 8.5px; font-weight: 700; color: #111; margin-top: 10px; }
  .about .about-text { font-size: 8.5px; color: #222; margin-top: 4px; }

  /* main column */
  .main { position: absolute; left: 174px; top: 208px; width: 348px; padding: 16px 0 0 16px; }
  .story h2 { font-family: "Roboto Condensed", Arial, sans-serif; font-weight: 700; color: var(--forest); font-size: 34px; line-height: 39px; letter-spacing: .2px; }
  .story--small h2 { font-size: 27px; line-height: 31px; }
  .story p { font-size: 10.2px; line-height: 18px; color: #333; width: 304px; }
  .story h2 + p { margin-top: 7px; }
  .subheading { display: flex; align-items: center; gap: 6px; font-family: "Arimo", Arial, sans-serif; font-weight: 700; font-size: 9.5px; color: var(--forest); margin: 6px 0 6px; letter-spacing: .2px; }
  .read-more { display: inline-flex; align-items: center; height: 22px; width: 94px; margin-top: 5px; position: relative; border: 1px solid #b5b54a; padding-left: 20px; font-size: 10px; color: #3a4a2a; }
  .read-more::before { content: ""; position: absolute; left: -1px; top: -1px; width: 0; height: 0; border-top: 11px solid transparent; border-bottom: 11px solid transparent; border-left: 9px solid #b5b54a; }
  .read-more::after { content: ""; position: absolute; left: -1px; top: 0; border-top: 10px solid transparent; border-bottom: 10px solid transparent; border-left: 8px solid #fff; }
  .story--small { margin-top: 28px; }

  .feature-photo { position: absolute; left: 174px; top: 765px; width: 348px; height: 117px; background: linear-gradient(90deg, #8b7a63, #c8b8a2 40%, #6d7d86 70%, #b59b84); border-top: 1px solid var(--rule); }
  .feature-label { position: absolute; left: 18px; bottom: 4px; background: #2a2a2a; color: var(--lemon); font-size: 10px; padding: 5px 12px 5px 16px; clip-path: polygon(8px 0, 100% 0, 100% 100%, 0 100%); }
  .corner-star { position: absolute; left: 160px; top: 752px; }
</style>
</head>
<body>

<article class="newsletter newsletter--leaf">
  <header class="masthead">
    <div class="brand-panel">
      <div class="brand-name">MERIDIAN<br>TRADE GROUP</div>
      <p class="brand-blurb">Editaquos rem restis dis imoditi ossitat urestius aut aut <u>pariberum</u> faccus <u>doloribus</u> aut prem repedis et eosam fuga.</p>
    </div>
    <div class="hero hero-leaf" role="img" aria-label="Photo of a leafy tree held in an open hand">
      <span class="issue-date">16 APRIL 2014</span>
      <div class="title-ribbon"><span class="newsletter-title">TRADEPOINT 411</span></div>
      <span class="hero-tagline">Your Source for the Latest in Trade Software and Technology News</span>
    </div>
  </header>

  <aside class="sidebar">
    <div class="social-bar"><span class="social-dot"></span><span class="social-dot"></span><span class="social-dot"></span><span class="social-dot"></span></div>
    <div class="site-url">www.meridiantrade.com</div>
    <nav class="contents">
      <div class="contents-item"><h4>ARTICLE 1</h4><p>Editaquos rem restis dis imoditi ossitat aut aut pariberum fuga.</p></div>
      <div class="contents-item"><h4>ARTICLE 2</h4><p>Editaquos rem restis dis imoditi ossitat aut aut pariberum fuga.</p></div>
      <div class="contents-item is-featured"><h4>FEATURED STORY</h4><p>Editaquos rem restis dis imoditi ossitat aut aut pariberum fuga.</p></div>
      <div class="contents-item"><h4>ARTICLE 3</h4><p>Editaquos rem restis dis imoditi ossitat aut aut pariberum fuga.</p></div>
    </nav>
    <section class="ceo-note">
      <div class="ceo-head">
        <div class="ceo-portrait" role="img" aria-label="Portrait photo of the CEO"></div>
        <div><div class="ceo-name">DANIEL REYES</div><div class="ceo-role">CEO</div></div>
      </div>
      <p>Editaquos rem restis dis imoditi ossitat urestius aut aut pariberum faccus doloribus aut prem repedis et eosam fuga. Giam quis quiae vel incid etur?</p>
      <p>Erchiliquo culparciame nobitates ma por rem exerrun tibusti doluptiore dipsuntus Iciendant id quossedit, ius consequia debit alit expellore sin erem vendita sperfernamus autetur?</p>
    </section>
    <section class="about">
      <h4>ABOUT US</h4>
      <svg width="34" height="40" viewBox="0 0 34 40" fill="none" stroke="#8a8a2a" stroke-width="1.6"><path d="M9 2v6M14 2v6M19 2v6"/><path d="M3 14h22v10a9 9 0 0 1-9 9h-4a9 9 0 0 1-9-9z"/><path d="M25 17h3a3 3 0 0 1 0 7h-3"/></svg>
      <div class="about-title">OMNIHILLES DERORRO VLAUT</div>
      <div class="about-text">Accabor eperum esciasi</div>
    </section>
  </aside>

  <main class="main">
    <section class="story">
      <h2>HEADING TITLE OF<br>THE ARTICLE BELOW</h2>
      <p>Lendae res nulpa cus, cum fugia volo quodipsus eiciis nullamus invera as et quiataq uoditin velent.</p>
      <p>Editaquos rem restis dis imoditi ossitat urestius aut aut pariberum faccus doloribus aut prem repedis et eosam fuga. It ipsum et quas dolorporiate natur se dolore eum ent modigen dandand anditate eicat apiet eicit omnis eum, arum evernat emquisti sus.</p>
      <p>Omnihilles derorro volo conse laut voloreh endite pre illa secabo.</p>
      <span class="read-more">READ MORE</span>
    </section>
    <section class="story story--small">
      <h2>SMALLER HEADING TITLE<br>FOR LONGER TITLE TEXT</h2>
      <div class="subheading"><svg width="24" height="8" viewBox="0 0 24 8"><path d="M0 4h21M17 1l4 3-4 3" stroke="#6a8a3a" stroke-width="1.4" fill="none"/></svg>HERE IS POSSIBLE SUBHEADING</div>
      <p>Lendae res nulpa cus, cum fugia volo quodipsus eiciis nullamus invera as et quiataq uoditin velent.</p>
      <p>Editaquos rem restis dis imoditi ossitat urestius aut aut pariberum faccus doloribus aut prem repedis et eosam fuga. It ipsum et quas dolorporiate natur se dolore eum ent modigen dandand anditate eicat apiet eicit omnis eum, arum evernat emquisti sus.</p>
      <p>Omnihilles derorro volo conse laut voloreh endite pre illa secabo.</p>
      <span class="read-more">READ MORE</span>
    </section>
  </main>

  <div class="feature-photo" role="img" aria-label="Photo of a team working together in an office">
    <span class="feature-label">FEATURED STORY</span>
  </div>
  <svg class="corner-star" width="30" height="30" viewBox="0 0 30 30"><path d="M15 1l4 10h10l-8 6 3 11-9-7-9 7 3-11-8-6h10z" fill="#f4ee8a" stroke="#c9c25a" stroke-width="1"/></svg>
</article>

<article class="newsletter newsletter--team">
  <header class="masthead">
    <div class="brand-panel">
      <div class="brand-name">MERIDIAN<br>TRADE GROUP</div>
      <p class="brand-blurb">Editaquos rem restis dis imoditi ossitat urestius aut aut <u>pariberum</u> faccus <u>doloribus</u> aut prem repedis et eosam fuga.</p>
    </div>
    <div class="hero hero-team" role="img" aria-label="Photo of business people in a meeting">
      <span class="issue-date">16 APRIL 2014</span>
      <div class="title-box">
        <div class="newsletter-title">TRADEPOINT 411</div>
        <div class="tag-strong">YOUR SOURCE FOR THE LATEST</div>
        <div class="tag-light">in Trade Software and Technology News</div>
      </div>
    </div>
  </header>

  <aside class="sidebar">
    <div class="social-bar"><span class="social-dot"></span><span class="social-dot"></span><span class="social-dot"></span><span class="social-dot"></span></div>
    <div class="site-url">www.meridiantrade.com</div>
    <nav class="contents">
      <div class="contents-item"><h4>ARTICLE 1</h4><p>Editaquos rem restis dis imoditi ossitat aut aut pariberum fuga.</p></div>
      <div class="contents-item"><h4>ARTICLE 2</h4><p>Editaquos rem restis dis imoditi ossitat aut aut pariberum fuga.</p></div>
      <div class="contents-item is-featured"><h4>FEATURED STORY</h4><p>Editaquos rem restis dis imoditi ossitat aut aut pariberum fuga.</p></div>
      <div class="contents-item"><h4>ARTICLE 3</h4><p>Editaquos rem restis dis imoditi ossitat aut aut pariberum fuga.</p></div>
    </nav>
    <section class="ceo-note">
      <div class="ceo-head">
        <div class="ceo-portrait" role="img" aria-label="Portrait photo of the CEO"></div>
        <div><div class="ceo-name">DANIEL REYES</div><div class="ceo-role">CEO</div></div>
      </div>
      <p>Editaquos rem restis dis imoditi ossitat urestius aut aut pariberum faccus doloribus aut prem repedis et eosam fuga. Giam quis quiae vel incid etur?</p>
      <p>Erchiliquo culparciame nobitates ma por rem exerrun tibusti doluptiore dipsuntus Iciendant id quossedit, ius consequia debit alit expellore sin erem vendita sperfernamus autetur?</p>
    </section>
    <section class="about">
      <h4>ABOUT US</h4>
      <svg width="34" height="40" viewBox="0 0 34 40" fill="none" stroke="#8a8a2a" stroke-width="1.6"><path d="M9 2v6M14 2v6M19 2v6"/><path d="M3 14h22v10a9 9 0 0 1-9 9h-4a9 9 0 0 1-9-9z"/><path d="M25 17h3a3 3 0 0 1 0 7h-3"/></svg>
      <div class="about-title">OMNIHILLES DERORRO VLAUT</div>
      <div class="about-text">Accabor eperum esciasi</div>
    </section>
  </aside>

  <main class="main">
    <section class="story">
      <h2>HEADING TITLE OF<br>THE ARTICLE BELOW</h2>
      <p>Lendae res nulpa cus, cum fugia volo quodipsus eiciis nullamus invera as et quiataq uoditin velent.</p>
      <p>Editaquos rem restis dis imoditi ossitat urestius aut aut pariberum faccus doloribus aut prem repedis et eosam fuga. It ipsum et quas dolorporiate natur se dolore eum ent modigen dandand anditate eicat apiet eicit omnis eum, arum evernat emquisti sus.</p>
      <p>Omnihilles derorro volo conse laut voloreh endite pre illa secabo.</p>
      <span class="read-more">READ MORE</span>
    </section>
    <section class="story story--small">
      <h2>SMALLER HEADING TITLE<br>FOR LONGER TITLE TEXT</h2>
      <div class="subheading"><svg width="24" height="8" viewBox="0 0 24 8"><path d="M0 4h21M17 1l4 3-4 3" stroke="#6a8a3a" stroke-width="1.4" fill="none"/></svg>HERE IS POSSIBLE SUBHEADING</div>
      <p>Lendae res nulpa cus, cum fugia volo quodipsus eiciis nullamus invera as et quiataq uoditin velent.</p>
      <p>Editaquos rem restis dis imoditi ossitat urestius aut aut pariberum faccus doloribus aut prem repedis et eosam fuga. It ipsum et quas dolorporiate natur se dolore eum ent modigen dandand anditate eicat apiet eicit omnis eum, arum evernat emquisti sus.</p>
      <p>Omnihilles derorro volo conse laut voloreh endite pre illa secabo.</p>
      <span class="read-more">READ MORE</span>
    </section>
  </main>

  <div class="feature-photo" role="img" aria-label="Photo of a team working together in an office">
    <span class="feature-label">FEATURED STORY</span>
  </div>
  <svg class="corner-star" width="30" height="30" viewBox="0 0 30 30"><path d="M15 1l4 10h10l-8 6 3 11-9-7-9 7 3-11-8-6h10z" fill="#f4ee8a" stroke="#c9c25a" stroke-width="1"/></svg>
</article>

</body>
</html>
```